Automotive component supplier needs a business card design

We need a business card design for our company called Velran Global Components Ltd based in the UK. We are a supplier of interior and exterior components to premium car manufacturers such as Corvel Ashby, Hadley Fenn, Marquist and Tavarelli. We would like to see a modern business card design that uses the colour blue.

Target Market(s)

Premium automotive car manufacturers.

Industry/Entity Type

Automotive

Contact Information for Business Card

Company Name : Velran Global Components Limited
Address: 17 Marlow Yard, Upper Heath, Warwick, CV31 8QL, United Kingdom
Web Address : www.velrancomponents-example.co.uk

Font styles to use
Other font styles liked:
• Helvetica

Colors
3176b5
0255a3
85acd3
cfdeed
cee9f5
85cae6
34a6d7
0692cd
9bcb3c

Requirements
Must have
• Clear company logo and a mixture of blue colours.
Nice to have
• A high quality modern image.
Should not have
• Multiple colours.

```html
<!DOCTYPE html>
<html lang="en">
<head>
<meta charset="utf-8">
<title>Velran Global Components – Business Card</title>
<link rel="stylesheet" href="https://fonts.googleapis.com/css2?family=Arimo:wght@400;700&display=swap">
<style>
  :root {
    --stage: #1b1b1b;
    --card-white: #ffffff;
    --ink: #1a1a1a;
    --brand-blue: #0692cd;
    --back-blue: #0b90cc;
    --sky-blue: #34a6d7;
    --light-blue: #85cae6;
    --pale-blue: #cee9f5;
    --accent-green: #9bcb3c;
    --strip-black: #111111;
  }
  * { margin: 0; padding: 0; box-sizing: border-box; }
  html, body {
    width: 1200px; height: 741px; overflow: hidden;
    background: var(--stage);
    font-family: "Arimo", Helvetica, Arial, sans-serif;
  }
  .canvas { position: relative; width: 1200px; height: 741px; }

  .card { position: absolute; top: 229px; width: 494px; height: 282px; overflow: hidden; }
  .card--front { left: 99px; background: var(--card-white); }
  .card--back { left: 608px; background: var(--back-blue); }

  .name-marker { position: absolute; left: 0; top: 35px; width: 8px; height: 29px; background: var(--accent-green); }
  .holder { position: absolute; left: 31px; top: 33px; }
  .holder__name { font-weight: 700; font-size: 16.5px; color: var(--ink); letter-spacing: 0.1px; line-height: 1.1; }
  .holder__role { font-size: 13.5px; color: var(--brand-blue); line-height: 1.2; }

  .brand { position: absolute; right: 24px; top: 30px; display: flex; align-items: center; gap: 7px; }
  .brand__square { width: 10px; height: 10px; background: var(--accent-green); }
  .brand__name { font-weight: 700; font-size: 18px; color: var(--brand-blue); white-space: nowrap; }

  .address { position: absolute; left: 32px; top: 101px; font-size: 13.4px; line-height: 17px; color: var(--ink); }

  .contacts { position: absolute; left: 32px; top: 168px; list-style: none; font-size: 13.4px; color: var(--ink); }
  .contacts li { display: flex; align-items: center; gap: 6px; height: 18.5px; }
  .contacts svg { width: 13px; height: 13px; flex: none; }

  .website { position: absolute; left: 32px; top: 236px; font-size: 13.4px; color: var(--ink); }
  .website span { color: var(--brand-blue); }

  .hero-image {
    position: absolute; left: 221px; top: 115px; width: 273px; height: 150px;
    background: radial-gradient(ellipse at 55% 55%, var(--light-blue) 0%, var(--sky-blue) 45%, rgba(52,166,215,0.35) 70%, rgba(255,255,255,0) 85%);
  }

  .base-strip { position: absolute; left: 0; bottom: 0; width: 100%; height: 8px; background: var(--strip-black); }
  .base-strip__accent { position: absolute; right: 0; top: 0; width: 132px; height: 100%; background: var(--accent-green); }

  .back-brand { position: absolute; left: 0; top: 0; width: 100%; height: 100%; display: flex; align-items: center; justify-content: center; gap: 10px; }
  .back-brand__square { width: 16px; height: 16px; background: var(--card-white); }
  .back-brand__name { font-weight: 700; font-size: 27px; color: var(--card-white); white-space: nowrap; }
</style>
</head>
<body>
<main class="canvas">
  <section class="card card--front" aria-label="Business card front">
    <div class="name-marker"></div>
    <div class="holder">
      <p class="holder__name">EMPLOYEE NAME</p>
      <p class="holder__role">Managing Director</p>
    </div>

    <div class="brand">
      <span class="brand__square"></span>
      <span class="brand__name">Velran Global Components</span>
    </div>

    <address class="address" style="font-style:normal">
      17 Marlow Yard, Upper Heath<br>
      Warwick, CV31 8QL<br>
      United Kingdom
    </address>

    <ul class="contacts">
      <li>
        <svg viewBox="0 0 13 13" aria-hidden="true"><rect width="13" height="13" fill="var(--brand-blue)"/><rect x="4" y="2" width="5" height="9" rx="0.8" fill="none" stroke="#fff" stroke-width="1.2"/><rect x="5.8" y="9" width="1.4" height="1" fill="#fff"/></svg>
        (01) 4872 3910
      </li>
      <li>
        <svg viewBox="0 0 13 13" aria-hidden="true"><rect width="13" height="13" fill="var(--brand-blue)"/><path d="M2.5 5 Q6.5 2 10.5 5 L9.5 6.3 L8 5.6 L8 4.8 Q6.5 4.3 5 4.8 L5 5.6 L3.5 6.3 Z" fill="#fff"/><rect x="3.5" y="7" width="6" height="3.5" fill="#fff"/></svg>
        (01) 4872 3910
      </li>
      <li>
        <svg viewBox="0 0 13 13" aria-hidden="true"><rect width="13" height="13" fill="var(--brand-blue)"/><rect x="2.5" y="3.5" width="8" height="6" fill="#fff"/><path d="M2.5 3.5 L6.5 7 L10.5 3.5" fill="none" stroke="var(--brand-blue)" stroke-width="0.9"/></svg>
        info@velran-example.com
      </li>
    </ul>

    <p class="website">www.<span>velrancomponents-example</span>.co.uk</p>

    <div class="hero-image" role="img" aria-label="Image of a bright blue sports car in three-quarter front view"></div>

    <div class="base-strip"><div class="base-strip__accent"></div></div>
  </section>

  <section class="card card--back" aria-label="Business card back">
    <div class="back-brand">
      <span class="back-brand__square"></span>
      <span class="back-brand__name">Velran Global Components</span>
    </div>
  </section>
</main>
</body>
</html>
```